Maplecrest Disability - Social Security Disability Attorneys

Our company is expanding to attract clients nationwide for our social security disability practice. We have a logo, but I am looking for a creative and elegant letterhead that projects an image of being technologically advanced but still professional enough for the legal field. I am looking for the "wow factor" combined with this is still professional enough for a law practice.

Requesting letterhead and business card design
Updates

Had to update and change the logo. The previous logo had a typo. Please send updates with the new logo for consideration. The letterhead and business cards should be professional enough to be used for a law firm. Thanks.

Industry/Entity Type

Law Practice, Law Firm, Healthcare Industry, Government

Colors

Designer to choose colors to be used in the design.

Requirements
Nice to have
• **Please create a vertical design for the business card**

```html
<!DOCTYPE html>
<html lang="en">
<head>
<meta charset="utf-8">
<title>Maplecrest Disability – Business Card</title>
<link rel="stylesheet" href="https://fonts.googleapis.com/css2?family=Montserrat:wght@400;500;600;700&display=swap">
<style>
  :root {
    --page-bg: #e8e2da;
    --card-light: #f4f5f8;
    --card-light-shade: #e4e6ec;
    --navy: #34479a;
    --band-top: #4866b3;
    --band-mid: #3d4f8e;
    --band-low: #4a66b2;
    --orange: #e8792a;
    --soft-white: #f2f2f4;
    --grey-text: #d3d6e0;
  }
  * { box-sizing: border-box; margin: 0; padding: 0; }
  html, body {
    width: 1200px; height: 943px; overflow: hidden;
    background: var(--page-bg);
  }
  .card {
    position: absolute; left: 384px; top: 93px;
    width: 432px; height: 756px;
    border-radius: 28px; overflow: hidden;
    border: 2px solid #ffffff;
    background: var(--card-light);
    box-shadow: 0 10px 30px rgba(60, 50, 40, 0.15);
    text-align: center;
    font-family: 'Montserrat', sans-serif;
  }
  .card-head {
    position: absolute; left: 0; top: 0; width: 100%; height: 261px;
    background: linear-gradient(180deg, var(--card-light-shade) 0%, var(--card-light) 60%, #ffffff 100%);
  }
  .brand-name {
    position: absolute; left: 0; top: 112px; width: 100%;
    font-weight: 600; font-size: 22px; letter-spacing: 1px;
    color: var(--navy);
  }
  .brand-tagline {
    position: absolute; left: 0; top: 146px; width: 100%;
    font-weight: 600; font-size: 9px; letter-spacing: 2.4px;
    color: var(--navy);
  }
  .card-band {
    position: absolute; left: 0; top: 261px; width: 100%; height: 495px;
    background: linear-gradient(180deg, var(--band-top) 0%, var(--band-mid) 45%, var(--band-mid) 70%, var(--band-low) 88%, var(--band-mid) 100%);
  }
  .person-name {
    position: absolute; left: 0; top: 40px; width: 100%;
    font-weight: 700; font-size: 26px; letter-spacing: -0.3px;
    color: var(--orange);
  }
  .person-role {
    position: absolute; left: 0; top: 76px; width: 100%;
    display: flex; justify-content: center; align-items: center; gap: 8px;
    font-weight: 400; font-size: 20px; line-height: 26px;
    color: var(--soft-white);
  }
  .person-role .rule { width: 62px; height: 2px; background: var(--orange); }
  .address {
    position: absolute; left: 0; top: 165px; width: 100%;
    font-size: 17px; line-height: 27px;
    color: var(--grey-text);
  }
  .icons {
    position: absolute; left: 0; top: 259px; width: 100%;
    display: flex; justify-content: center;
  }
  .icon {
    width: 31px; height: 29px; background: var(--orange);
    display: flex; align-items: center; justify-content: center;
  }
  .icon.mail { margin-left: 47px; }
  .icon.web { margin-left: 34px; }
  .contacts {
    position: absolute; left: 0; top: 318px; width: 100%;
    font-size: 18px; line-height: 30px;
    color: var(--soft-white);
  }
</style>
</head>
<body>
  <div class="card">
    <header class="card-head">
      <div class="brand-name">MAPLECREST DISABILITY</div>
      <div class="brand-tagline">SOCIAL SECURITY DISABILITY ATTORNEYS</div>
    </header>
    <section class="card-band">
      <div class="person-name">DANIEL WHITCOMBE</div>
      <div class="person-role"><span class="rule"></span>Co-Founder<span class="rule"></span></div>
      <div class="address">Suite 4, Level 18, Elmwood<br>Street Brookvale NSW 2100</div>
      <div class="icons">
        <span class="icon phone">
          <svg width="18" height="18" viewBox="0 0 24 24"><path fill="#fff" d="M6.6 10.8a15.1 15.1 0 0 0 6.6 6.6l2.2-2.2a1 1 0 0 1 1-.25 11.4 11.4 0 0 0 3.6.57 1 1 0 0 1 1 1V20a1 1 0 0 1-1 1A17 17 0 0 1 3 4a1 1 0 0 1 1-1h3.5a1 1 0 0 1 1 1c0 1.25.2 2.45.57 3.57a1 1 0 0 1-.25 1z"/></svg>
        </span>
        <span class="icon mail">
          <svg width="20" height="14" viewBox="0 0 22 16"><rect x="1" y="1" width="20" height="14" fill="none" stroke="#fff" stroke-width="1.6"/><path d="M1 1l10 8 10-8" fill="none" stroke="#fff" stroke-width="1.6"/></svg>
        </span>
        <span class="icon web">
          <svg width="18" height="18" viewBox="0 0 20 20"><circle cx="10" cy="10" r="8.5" fill="none" stroke="#fff" stroke-width="1.6"/><ellipse cx="10" cy="10" rx="3.6" ry="8.5" fill="none" stroke="#fff" stroke-width="1.3"/><path d="M1.5 10h17" stroke="#fff" stroke-width="1.3"/></svg>
        </span>
      </div>
      <div class="contacts">
        555-214-7730<br>
        info@maplecrestdisability.com<br>
        www.maplecrestdisability.com
      </div>
    </section>
  </div>
</body>
</html>
```